Brightfen Business Card Redesign & Logo Update

We need to update our business cards to something more modern and fresh. Brightfen can provide the current color schemes and old design examples, but welcome creativity in helping us with this redesign. PLEASE NOTE that we no longer utilize the "tree" and/or "leaf" imagery in our branding. If able would apprecaite an update on the quality of our "words only" logo in Ai. / PNG formats too.

Target Market(s)

Investors, landowners, corporate partners, contractors

Industry/Entity Type

Environmental Restoration & Conservation

Contact Information for Business Card

Logo, persons name, title, mailing address, phone and email, website url

Font styles to use
Other font styles liked:
• Merriweather

Requirements
Nice to have
• Logo, persons name, title, mailing address, phone and email, website url, but open to ideams
Should not have
• No all back backgrounds

```html
<!DOCTYPE html>
<html lang="en">
<head>
<meta charset="utf-8">
<title>Brightfen Business Cards</title>
<link rel="stylesheet" href="https://fonts.googleapis.com/css2?family=Merriweather:wght@400;700;900&display=swap">
<style>
  :root {
    --brand-orange: #ee7f22;
    --brand-green: #1b7b42;
    --ink: #222222;
    --paper: #ffffff;
    --backdrop: #e6e7e9;
  }
  * { box-sizing: border-box; margin: 0; padding: 0; }
  html, body {
    width: 1200px;
    height: 1059px;
    overflow: hidden;
    background: var(--backdrop);
    font-family: "Merriweather", Georgia, serif;
    color: var(--ink);
  }
  .sheet { position: relative; width: 1200px; height: 1059px; }

  .card {
    position: absolute;
    width: 640px;
    height: 366px;
    background: var(--paper);
    box-shadow: 0 10px 30px rgba(0,0,0,0.18);
    overflow: hidden;
  }
  .card--front { left: 90px; top: 80px; }
  .card--back  { left: 470px; top: 580px; }

  .wordmark {
    font-family: "Merriweather", Georgia, serif;
    font-weight: 900;
    color: var(--brand-green);
    letter-spacing: 1px;
    text-transform: uppercase;
    line-height: 1;
    white-space: nowrap;
  }
  .card--front .wordmark {
    position: absolute;
    left: 0; right: 0; top: 50%;
    transform: translateY(-50%);
    text-align: center;
    font-size: 58px;
  }

  .card__wave { position: absolute; inset: 0; width: 100%; height: 100%; }

  .card__divider {
    position: absolute;
    left: 330px; top: 34px;
    width: 2px; height: 150px;
    background: var(--brand-orange);
  }
  .card--back .wordmark {
    position: absolute;
    left: 360px; top: 82px;
    font-size: 34px;
  }

  .contact {
    position: absolute;
    left: 0; top: 88px;
    width: 320px;
    padding-left: 42px;
  }
  .contact__accent {
    position: absolute;
    left: 0; top: 6px;
    width: 14px; height: 40px;
    background: var(--brand-orange);
  }
  .contact__name {
    font-size: 19px;
    font-weight: 900;
    letter-spacing: 0.5px;
    text-transform: uppercase;
  }
  .contact__name .first { color: var(--brand-orange); }
  .contact__name .last  { color: var(--brand-green); }
  .contact__title { font-size: 14px; margin-top: 4px; }
  .contact__address { font-size: 14px; line-height: 1.45; margin-top: 18px; }
  .contact__list { list-style: none; margin-top: 18px; font-size: 14px; }
  .contact__list li { display: flex; align-items: center; gap: 8px; line-height: 1.65; }
  .contact__icon { width: 14px; height: 14px; flex: none; }
</style>
</head>
<body>
<main class="sheet">

  <section class="card card--front" aria-label="Business card front">
    <div class="wordmark">Brightfen</div>
  </section>

  <section class="card card--back" aria-label="Business card back">
    <svg class="card__wave" viewBox="0 0 640 366" preserveAspectRatio="none" aria-hidden="true">
      <path d="M0 310 C 170 300, 300 320, 420 245 S 580 120, 640 108 L640 366 L0 366 Z" fill="var(--brand-green)"/>
      <path d="M40 312 C 200 305, 300 300, 410 232 S 560 110, 640 92 L640 100 C 565 118, 430 210, 405 232 C 300 310, 200 312, 40 312 Z" fill="var(--brand-orange)"/>
    </svg>

    <div class="card__divider"></div>
    <div class="wordmark">Brightfen</div>

    <div class="contact">
      <span class="contact__accent"></span>
      <div class="contact__name"><span class="first">Marcus</span> <span class="last">Vale</span></div>
      <div class="contact__title">Founder</div>
      <p class="contact__address">48 Marsh Lane, Suite 12<br>PO Box 2917, Fen County</p>
      <ul class="contact__list">
        <li>
          <svg class="contact__icon" viewBox="0 0 16 16" aria-hidden="true"><path fill="var(--brand-orange)" d="M3 1.5l3 .5 1 3-1.6 1.4a9 9 0 0 0 4.2 4.2L11 9l3 1 .5 3-1.5 1.5C7 14.5 1.5 9 1.5 3Z"/></svg>
          (555) 204-3187
        </li>
        <li>
          <svg class="contact__icon" viewBox="0 0 16 16" aria-hidden="true"><rect x="1" y="3" width="14" height="10" rx="1" fill="var(--brand-orange)"/><path d="M1.5 4l6.5 5 6.5-5" stroke="#fff" stroke-width="1.4" fill="none"/></svg>
          hello@brightfen.com
        </li>
        <li>
          <svg class="contact__icon" viewBox="0 0 16 16" aria-hidden="true"><circle cx="8" cy="8" r="7" fill="var(--brand-orange)"/><path d="M1 8h14M8 1c3 3 3 11 0 14M8 1c-3 3-3 11 0 14" stroke="#fff" stroke-width="1" fill="none"/></svg>
          www.brightfen.com
        </li>
      </ul>
    </div>
  </section>

</main>
</body>
</html>
```